20 year old business card needs re-design

We need to redesign our corporate business card look. We need something that appears more modern, eye catchy but professional.

Target Market(s)

manufacturing industry

Industry/Entity Type

Manufacturer

Contact Information for Business Card

One side can have the logo. Other side can have contact information.

Font styles to use
Serif

Colors
3277b5
33b8a4
ffffff

Requirements
Must have
• Eye catchy - need to standout from the crowd. company logo cannot change. Full name, job title, phone number and email address.
Should not have
• Fax, business address is not necessary.

```html
<!DOCTYPE html>
<html lang="en">
<head>
<meta charset="utf-8">
<title>Corvale Business Card</title>
<link href="https://fonts.googleapis.com/css2?family=Montserrat:wght@500;800&family=Open+Sans:wght@400&display=swap" rel="stylesheet">
<style>
  :root {
    --brand-blue: #3277b5;
    --brand-teal: #33b8a4;
    --white: #ffffff;
    --ink: #231f20;
    --muted: #6d6e71;
    --backdrop: #e5e5e5;
  }
  * { margin: 0; padding: 0; box-sizing: border-box; }
  html, body {
    width: 1200px; height: 1000px; overflow: hidden;
    background: var(--backdrop);
  }
  .canvas { position: relative; width: 1200px; height: 1000px; }
  .card {
    position: absolute; left: 239px; width: 698px; height: 398px;
    border-radius: 14px; overflow: hidden;
  }
  .card--front { top: 82px; background: var(--white); }
  .card--back { top: 520px; background: var(--brand-blue); }

  .wordmark {
    position: absolute;
    font-family: "Montserrat", sans-serif; font-weight: 800;
    letter-spacing: -1px; line-height: 1;
  }
  .card--front .wordmark { left: 60px; top: 160px; font-size: 56px; color: var(--ink); }
  .card--back .wordmark { left: 0; right: 0; top: 158px; text-align: center; font-size: 66px; color: var(--white); }

  .divider { position: absolute; left: 333px; width: 3px; }
  .divider--name { top: 136px; height: 44px; background: var(--brand-blue); }
  .divider--contact { top: 200px; height: 61px; width: 2px; background: var(--brand-teal); }

  .person { position: absolute; left: 362px; top: 133px; }
  .person__name {
    font-family: "Montserrat", sans-serif; font-weight: 500;
    font-size: 22px; letter-spacing: 0.5px; color: var(--brand-blue);
  }
  .person__title {
    font-family: "Open Sans", sans-serif; font-size: 14.5px;
    color: var(--muted); margin-top: 2px;
  }

  .contact-list { position: absolute; left: 360px; top: 198px; list-style: none; }
  .contact-list li {
    display: flex; align-items: center; height: 22px;
    font-family: "Open Sans", sans-serif; font-size: 15px; color: var(--muted);
  }
  .contact-list svg { width: 14px; height: 14px; margin-right: 11px; fill: var(--brand-blue); }

  .wave { position: absolute; left: 0; bottom: 0; width: 698px; height: 60px; }

  .web-address {
    position: absolute; left: 0; right: 0; top: 346px; text-align: center;
    font-family: "Open Sans", sans-serif; font-size: 15px;
    letter-spacing: 1px; color: var(--white);
  }
</style>
</head>
<body>
<main class="canvas">
  <section class="card card--front" aria-label="Business card front">
    <div class="wordmark">Corvale</div>

    <span class="divider divider--name"></span>
    <div class="person">
      <div class="person__name">DANA MERROW</div>
      <div class="person__title">Sr. Project Manager</div>
    </div>

    <span class="divider divider--contact"></span>
    <ul class="contact-list">
      <li>
        <svg viewBox="0 0 14 14" aria-hidden="true"><path d="M4 0h6a1 1 0 0 1 1 1v12a1 1 0 0 1-1 1H4a1 1 0 0 1-1-1V1a1 1 0 0 1 1-1zm.5 1.5v9.5h5V1.5z"/></svg>
        555-014-7200 xt 118
      </li>
      <li>
        <svg viewBox="0 0 14 14" aria-hidden="true"><path d="M1 3h12v1L7 8 1 4z M1 5.3l6 4 6-4V11H1z"/></svg>
        dana@corvaleworks.com
      </li>
      <li>
        <svg viewBox="0 0 14 14" aria-hidden="true"><path d="M6 1a5 5 0 0 1 4 8l3.3 3.3-1.2 1.2L8.8 10.2A5 5 0 1 1 6 1zm0 2a3 3 0 1 0 0 6 3 3 0 0 0 0-6z"/></svg>
        CorvaleWorks.com
      </li>
    </ul>

    <svg class="wave" viewBox="0 0 698 60" preserveAspectRatio="none" aria-hidden="true">
      <path d="M270 24 Q500 20 698 34 L698 58 Q560 40 270 24 Z" fill="var(--brand-teal)"/>
      <path d="M0 35 Q380 12 698 60 L0 60 Z" fill="var(--brand-blue)"/>
      <path d="M300 24 Q560 30 692 56" fill="none" stroke="var(--white)" stroke-width="1.5"/>
    </svg>
  </section>

  <section class="card card--back" aria-label="Business card back">
    <div class="wordmark">Corvale</div>
    <div class="web-address">corvaleworks.com</div>
  </section>
</main>
</body>
</html>
```